Meridale Bed Company Needs Business Card

Looking for a very nice looking business card. Creative but not extravagant. We sell beds and pillows across the U.S. and need something professional but catchy. I have attached the logo.

Name : Devin Holt
Title : President
Phone : (800) 471-2960
Email: sleep@quilmora.com
Website: www.quilmora.com

Can be single-sided or double-sided
horizontal or vertical

Can use Blues/Greys

Target Market(s)

Mass Market

Industry/Entity Type

Retail

Contact Information for Business Card

Name : Devin Holt
Title : President
Phone : (800) 471-2960
Email: sleep@quilmora.com
Website: www.quilmora.com

Requirements
Must have
• Clean, Modern, Smooth
• Can use Blues/Greys
• On the other side without the information - have something simple like www.quilmora.com or our logo
Nice to have
• Surprise me
Should not have
• Nothing crazy, nothing cluttered

```html
<!DOCTYPE html>
<html lang="en">
<head>
<meta charset="utf-8">
<title>Quilmora Business Card</title>
<link rel="stylesheet" href="https://fonts.googleapis.com/css2?family=Open+Sans:wght@300;400;600&display=swap">
<style>
  :root {
    --stage: #ebe7e1;
    --card-dark: #353537;
    --card-light: #cfcfcf;
    --card-light-deep: #b6b6b6;
    --accent-blue: #5da2d6;
    --text-dark: #2e2e30;
    --text-white: #f2f2f2;
    --text-muted: #b9b9b9;
  }
  * { margin: 0; padding: 0; box-sizing: border-box; }
  html, body {
    width: 1200px; height: 843px; overflow: hidden;
    background: var(--stage);
    font-family: "Open Sans", sans-serif;
  }
  .canvas { position: relative; width: 1200px; height: 843px; }
  .card {
    position: absolute; top: 267px; width: 540px; height: 309px;
    overflow: hidden; border-radius: 2px;
    box-shadow: 0 10px 24px rgba(0,0,0,0.18);
  }
  .card-front { left: 40px; }
  .card-back { left: 620px; background: var(--card-dark); }
  .card-shapes { position: absolute; inset: 0; width: 100%; height: 100%; }

  .name-block { position: absolute; left: 46px; top: 93px; }
  .person-name { font-size: 21px; font-weight: 600; color: var(--text-white); line-height: 1.1; }
  .person-title { font-size: 12px; font-weight: 400; color: var(--text-muted); margin-top: 2px; }

  .contact-list { position: absolute; left: 40px; top: 160px; list-style: none; }
  .contact-item {
    display: flex; align-items: center; gap: 10px;
    font-size: 15px; color: var(--text-dark); height: 25px;
  }
  .contact-icon { width: 17px; height: 17px; flex: none; }

  .front-wordmark {
    position: absolute; left: 354px; top: 214px;
    font-size: 30px; font-weight: 300; color: var(--accent-blue);
    letter-spacing: 1px; line-height: 1;
  }
  .back-wordmark {
    position: absolute; left: 0; right: 0; top: 50%;
    transform: translateY(-50%);
    text-align: center;
    font-size: 92px; font-weight: 300; color: var(--accent-blue);
    letter-spacing: 3px; line-height: 1;
  }
</style>
</head>
<body>
<div class="canvas">

  <section class="card card-front" aria-label="Business card front">
    <svg class="card-shapes" viewBox="0 0 540 309" preserveAspectRatio="none" aria-hidden="true">
      <defs>
        <linearGradient id="lightFace" x1="0" y1="0" x2="1" y2="1">
          <stop offset="0" stop-color="var(--card-light)"/>
          <stop offset="1" stop-color="var(--card-light-deep)"/>
        </linearGradient>
      </defs>
      <rect class="face" width="540" height="309" fill="url(#lightFace)"/>
      <!-- right corner strip -->
      <polygon class="corner-strip" points="470,0 540,0 540,205 498,205" fill="#d8d8d8"/>
      <!-- dark sweep -->
      <path class="dark-sweep" d="M272 0 L470 0 L498 205 L388 205 Q372 90 272 0 Z" fill="var(--card-dark)"/>
      <!-- blue arc -->
      <path class="accent-arc" d="M232 0 L272 0 Q372 90 388 205 L368 205 Q346 80 232 0 Z" fill="var(--accent-blue)"/>
      <!-- name bar -->
      <polygon class="name-bar" points="20,86 300,86 312,130 20,130" fill="var(--card-dark)"/>
      <line class="name-bar-line" x1="0" y1="133" x2="314" y2="133" stroke="var(--accent-blue)" stroke-width="3"/>
      <line class="name-divider" x1="34" y1="96" x2="34" y2="124" stroke="#9a9a9a" stroke-width="1"/>
      <!-- bottom band with tab -->
      <path class="bottom-band" d="M0 258 L322 258 L338 207 L540 207 L540 309 L0 309 Z" fill="var(--card-dark)"/>
      <path class="band-line" d="M0 258 L322 258 L338 207 L540 207" fill="none" stroke="var(--accent-blue)" stroke-width="4"/>
    </svg>

    <div class="name-block">
      <p class="person-name">Devin Holt</p>
      <p class="person-title">President</p>
    </div>

    <ul class="contact-list">
      <li class="contact-item">
        <svg class="contact-icon" viewBox="0 0 16 16" aria-hidden="true">
          <rect width="16" height="16" rx="3" fill="var(--text-dark)"/>
          <path d="M5 3.5 L6.6 5.6 L5.7 6.8 Q6.8 9 9.2 10.3 L10.4 9.4 L12.5 11 L11.4 12.6 Q7.6 12.4 4.6 8.6 Q3.4 6.2 5 3.5 Z" fill="#fff"/>
        </svg>
        <span>(800) 471-2960</span>
      </li>
      <li class="contact-item">
        <svg class="contact-icon" viewBox="0 0 16 16" aria-hidden="true">
          <rect x="1" y="3.5" width="14" height="9" fill="none" stroke="var(--text-dark)" stroke-width="1.2"/>
          <path d="M1 3.5 L8 9 L15 3.5 M1 12.5 L6 8 M15 12.5 L10 8" fill="none" stroke="var(--text-dark)" stroke-width="1.2"/>
        </svg>
        <span>sleep@quilmora.com</span>
      </li>
      <li class="contact-item">
        <svg class="contact-icon" viewBox="0 0 16 16" aria-hidden="true">
          <circle cx="8" cy="8" r="6.5" fill="none" stroke="var(--text-dark)" stroke-width="1.1"/>
          <ellipse cx="8" cy="8" rx="3" ry="6.5" fill="none" stroke="var(--text-dark)" stroke-width="1"/>
          <path d="M1.5 8 H14.5 M2.5 5 H13.5 M2.5 11 H13.5" stroke="var(--text-dark)" stroke-width="1"/>
        </svg>
        <span>www.quilmora.com</span>
      </li>
    </ul>

    <p class="front-wordmark">quilmora</p>
  </section>

  <section class="card card-back" aria-label="Business card back">
    <p class="back-wordmark">quilmora</p>
  </section>

</div>
</body>
</html>
```